San Francisco Leading Consulting firm - 47Vora Web Design Project

•Create a Web Design
•Uncoded webpage layout design
•2 Pages Design - Homepage + Interior Page

Task Description
Hello, we're looking for a re-design our current website www.47vora-example.com

we have a sample mockup design @

http://47vora.pubtrellis-example.org/

This shows the layout that we like and also a sample of 6 pictures that would change based on where you mouse over..

6 pictures HOME design needs to be included.

SMART
THOUGHTFUL
FLEXIBLE
CREATIVE SERVICES
TECHNICAL SERVICES
PARTNERS

sites we like:

http://www.melvanadvisory-example.com/Home.cfm?id=Home
http://www.plinthworks-example.com/index.html

Our company can be best described as: 100+ employees, cutting-edge, depandable, innovative, strong, smart.

Our Primary focus is: IT Consulting Services and Creative Design services

47Vora LLC is a consulting firm providing creative design, business and technology solutions to both private and public interests.

Established in 1996, 47Vora is a San Francisco based company providing specialists for a range of business needs including:

Creative Design Services
•Print
•Logo Design
•Website Design
•Illustration

and

Business and Technology solutions

•Application Software and Web Development
•Business Process Re-Design (BPR)
•Business/Systems Analysis and Requirement Documentation
•Mentoring and Training
•Network/Hardware Installation Services
•System Design and Architecture
•Vendor Management
•Docuvault Architecture and Implementation

our sample mockup site:

Reason: Due to holiday season, we're not available to work with designers and finilize our design.  

Thank you very much for submitting your design.

We appreciate your time and creativity.   Since, our office is currently closed for holidays, we will be reviewing it in details next week and will make our decision as soon as possible.

It would be great if you could submit any of your changes by Wed next week, so it would be part of our reviews. 

Please see updated wireframe under attachments:  we have some minor updates to our wireframe that we would like you to update your designs, if possible.  

We also encorouge you not to use our standard wireframe and come up with more unique designs.   Everything would be considered when we review your design.

 

Orbis Market(s)

Creative services and professional services clients, including government agencies

Industry/Entity Type

Business

Requirements
Must have
• Clean, professional look, easy navigation

```html
<!DOCTYPE html>
<html lang="en">
<head>
<meta charset="utf-8">
<title>47Vora – Creative, Business and Technology Solutions</title>
<link rel="stylesheet" href="https://fonts.googleapis.com/css2?family=Arimo:wght@400;700&family=Barlow+Condensed:wght@500&display=swap">
<style>
:root{
  --green:#5cb21c;
  --green-dark:#3f9a12;
  --green-bright:#7ed321;
  --ink:#1e1e1e;
  --text:#444;
  --muted:#7a7a7a;
  --rule:#b5b5b5;
  --photo-light:#d8d8d8;
  --photo-mid:#8f8f8f;
  --photo-dark:#4a4a4a;
  --white:#fff;
}
*{box-sizing:border-box;margin:0;padding:0}
html,body{width:1200px;height:1100px;overflow:hidden;background:var(--white)}
body{position:relative;font-family:Arimo,Helvetica,Arial,sans-serif;color:var(--text)}
a{text-decoration:none;color:inherit}
.abs{position:absolute}

/* header */
.site-header{position:absolute;left:0;top:0;width:1200px;height:98px;border-bottom:1px solid #8a8a8a}
.brand{position:absolute;left:132px;top:18px;display:flex;align-items:center;gap:10px}
.brand-dot{width:34px;height:34px;border-radius:50%;background:var(--green)}
.brand-name{font-size:30px;color:#555;letter-spacing:1px}
.contact{position:absolute;top:4px;left:813px;font-size:12px;line-height:18px;color:var(--muted)}
.contact .hi{color:var(--green);font-weight:700;position:absolute;left:149px;white-space:nowrap}
.main-nav{position:absolute;top:70px;left:0;font-size:13px;color:#444}
.main-nav a{position:absolute;white-space:nowrap}
.main-nav .current{color:var(--green)}
.nav-pointer{position:absolute;left:438px;top:90px;width:0;height:0;border-left:5px solid transparent;border-right:5px solid transparent;border-bottom:7px solid var(--green)}

/* hero */
.hero-photo{position:absolute;left:0;top:98px;width:1200px;height:569px;background:linear-gradient(180deg,var(--photo-light) 0%,var(--photo-mid) 55%,var(--photo-dark) 100%)}
.slide{position:absolute;left:139px;top:160px;width:920px;height:329px;background:var(--white);border-radius:6px 6px 0 0}
.slide-head{position:absolute;left:79px;top:122px;font-family:"Barlow Condensed","Arial Narrow",sans-serif;font-weight:500;font-size:38px;line-height:38px;color:var(--ink)}
.slide-head .accent{display:block;color:var(--green);margin-left:3px}
.slide-art{position:absolute;left:560px;top:4px;width:270px;height:305px;border-radius:50%;background:radial-gradient(circle at 55% 60%,#d3202a 0%,#e8e8e8 45%,var(--white) 72%)}
.arrow{position:absolute;top:302px;width:34px;height:64px;background:var(--white)}
.arrow.prev{left:107px;border-radius:32px 0 0 32px}
.arrow.next{left:1058px;border-radius:0 32px 32px 0}
.arrow svg{position:absolute;top:16px}
.dots{position:absolute;top:500px;left:520px;display:flex;gap:12px;align-items:center}
.dots span{width:15px;height:15px;border-radius:50%;background:var(--white)}
.dots .on{width:18px;height:18px;background:var(--green-bright);border:2px solid #4d8e12}

/* service cards */
.card{position:absolute;top:603px;width:300px;height:108px;background:linear-gradient(180deg,#e6e6e6 0%,var(--white) 55%);border-radius:4px 4px 0 0;box-shadow:0 2px 4px rgba(0,0,0,.25)}
.card h3{position:absolute;font-size:15px;font-weight:700;color:#4a4a4a;line-height:18px}
.card .more{position:absolute;font-size:11px;font-weight:700;color:var(--green);letter-spacing:.3px}
.card svg{position:absolute}

/* clients */
.clients-title{position:absolute;left:127px;top:766px;font-size:18px;font-weight:700;line-height:20px;color:#333}
.client{position:absolute;top:773px;font-size:15px;font-weight:700;color:#777;text-align:center;width:80px}
.latest{position:absolute;left:875px;top:745px;height:76px;border-left:1px solid var(--rule);padding-left:26px}
.latest h4{font-size:15px;color:var(--ink);margin-top:5px}
.latest .date{font-size:12px;font-weight:700;color:var(--green);margin-top:6px;letter-spacing:.3px}
.latest p{font-size:13px;color:#333;line-height:16px}

.rule{position:absolute;left:122px;width:960px;height:1px;background:var(--rule)}
.services-list{position:absolute;list-style:none;font-size:13px;line-height:24px;color:#4a4a4a}

/* footer */
.copyright{position:absolute;left:119px;top:987px;font-size:12px;font-weight:700;color:#333}
.footer-nav a{position:absolute;top:987px;font-size:12px;font-weight:700;color:var(--green-dark)}
</style>
</head>
<body>

<header class="site-header">
  <a class="brand" href="#"><span class="brand-dot"></span><span class="brand-name">47Vora</span></a>
  <div class="contact">
    <div>1720 Harlow Ave, Ste 410 <span class="hi">415-555-0142</span></div>
    <div>San Francisco, CA 94107 <span class="hi">info@47vora-example.com</span></div>
  </div>
  <nav class="main-nav">
    <a class="current" style="left:429px">Home</a>
    <a style="left:503px">Company</a>
    <a style="left:596px">Creative Services</a>
    <a style="left:737px">Technical Services</a>
    <a style="left:886px">Partners</a>
    <a style="left:974px">Contact Us</a>
  </nav>
  <span class="nav-pointer"></span>
</header>

<section class="hero">
  <div class="hero-photo" role="img" aria-label="Black and white aerial photo of the San Francisco skyline"></div>
  <div class="slide">
    <h1 class="slide-head">YOU HAVE COMPLEX ISSUES.<span class="accent">We create versatile solutions.</span></h1>
    <div class="slide-art" role="img" aria-label="Red multi-tool pocket knife with blades opened out"></div>
  </div>
  <a class="arrow prev" href="#" aria-label="Previous slide"><svg width="26" height="34" style="left:6px"><path d="M20 2 L6 17 L20 32" fill="none" stroke="var(--green)" stroke-width="6"/></svg></a>
  <a class="arrow next" href="#" aria-label="Next slide"><svg width="26" height="34" style="left:2px"><path d="M6 2 L20 17 L6 32" fill="none" stroke="var(--green)" stroke-width="6"/></svg></a>
  <div class="dots"><span class="on"></span><span></span><span></span><span></span><span></span><span></span></div>
</section>

<section class="services">
  <article class="card" style="left:129px">
    <svg width="40" height="40" style="left:28px;top:12px"><path d="M20 36 C6 30 6 14 20 4 C34 14 34 30 20 36Z" fill="none" stroke="#666" stroke-width="2"/><path d="M20 36 L20 12" stroke="#666" stroke-width="2"/></svg>
    <h3 style="left:110px;top:22px">Creative Services</h3>
    <a class="more" style="left:186px;top:63px">LEARN MORE</a>
  </article>
  <article class="card" style="left:449px">
    <svg width="40" height="40" style="left:26px;top:16px"><path d="M6 34 L30 10 M10 8 L34 32" stroke="#555" stroke-width="5" stroke-linecap="round"/></svg>
    <h3 style="left:120px;top:22px">Business &amp; Technical<br>Services</h3>
    <a class="more" style="left:189px;top:62px">LEARN MORE</a>
  </article>
  <article class="card" style="left:770px">
    <svg width="46" height="42" style="left:24px;top:14px"><circle cx="14" cy="14" r="9" fill="none" stroke="#555" stroke-width="5" stroke-dasharray="3 2"/><circle cx="32" cy="30" r="7" fill="none" stroke="#555" stroke-width="5" stroke-dasharray="3 2"/></svg>
    <h3 style="left:132px;top:22px">Corporate Partners</h3>
    <a class="more" style="left:197px;top:62px">LEARN MORE</a>
  </article>
</section>

<section class="clients">
  <h2 class="clients-title">Featured<br>Clients</h2>
  <svg class="abs" style="left:208px;top:762px" width="30" height="48"><path d="M4 2 L26 24 L4 46 L12 24Z" fill="var(--green)"/></svg>
  <span class="client" style="left:240px">Kestrel</span>
  <span class="client" style="left:317px">Orbis</span>
  <span class="client" style="left:388px">Lumora</span>
  <span class="client" style="left:457px">Ferro</span>
  <span class="client" style="left:531px">Vexa</span>
  <span class="client" style="left:610px">Talon</span>
  <span class="client" style="left:689px">Brava</span>
  <span class="client" style="left:776px">Hollin</span>
  <aside class="latest">
    <h4>Latest Project <svg width="12" height="14" style="margin-left:14px"><path d="M3 1 L9 7 L3 13" fill="none" stroke="var(--green)" stroke-width="3"/></svg></h4>
    <div class="date">JANUARY 19, 2011</div>
    <p>Lorem ipsum dolor sit amet,<br>consectetur adipiscing elit.</p>
  </aside>
</section>

<div class="rule" style="top:837px"></div>

<ul class="services-list" style="left:132px;top:855px">
  <li>Application Software and Web Development</li>
  <li>Business Process Re-Design (BPR)</li>
  <li>Systems Analysis and Requirement Docs</li>
  <li>Mentoring and Training</li>
</ul>
<ul class="services-list" style="left:456px;top:853px">
  <li>Network/Hardware Installation Services</li>
  <li>System Design and Architecture</li>
  <li>Vendor Management</li>
  <li>Docuvault Architecture and Implementation</li>
</ul>
<ul class="services-list" style="left:780px;top:848px">
  <li>Print &amp; Package Design</li>
  <li>Brand and Identity Creation</li>
  <li>Website and User Experience Design</li>
  <li>Illustration Design</li>
</ul>

<div class="rule" style="top:967px"></div>

<footer>
  <p class="copyright">Copyright 2011, 47Vora, LLC All rights reserved.</p>
  <nav class="footer-nav">
    <a style="left:516px">Home</a>
    <a style="left:580px">Company</a>
    <a style="left:665px">Technical Services</a>
    <a style="left:804px">Creative Services</a>
    <a style="left:937px">Partners</a>
    <a style="left:1017px">Contact Us</a>
  </nav>
</footer>

</body>
</html>
```